Coastline Premier Retreats Business Card Design

Design a business card for Coastline Premier Retreats. Look at the website for colors and reference. Card should have logo, name, title, office number, mobile number, email, URL and a tagline like, "Luxury Hotel & Resort Email Marketing" (This might change).

https://www.coastlinepremierretreats.example

The rest I will leave up to your imagination.

Contact Information for Business Card

Logo, name, title, office number, mobile number, email, URL and a tagline like, "Luxury Hotel & Resort Email Marketing" (This might change).

```html
<!DOCTYPE html>
<html lang="en">
<head>
<meta charset="utf-8">
<title>Coastline Premier Retreats — Business Card</title>
<link href="https://fonts.googleapis.com/css2?family=Open+Sans:wght@400;600;700&display=swap" rel="stylesheet">
<style>
  :root {
    --backdrop: #232324;
    --card: #1e1e21;
    --card-back: #1b1b1e;
    --orange: #f07622;
    --white: #f4f4f4;
    --emboss: #2a2a2e;
  }
  * { margin: 0; padding: 0; box-sizing: border-box; }
  html, body {
    width: 1200px; height: 780px; overflow: hidden;
    background: var(--backdrop);
    font-family: "Open Sans", Arial, sans-serif;
  }
  .stage {
    width: 1200px; height: 780px;
    display: flex; align-items: center; justify-content: center; gap: 40px;
  }
  .card {
    position: relative;
    width: 540px; height: 309px;
    border-radius: 3px;
    box-shadow: 0 18px 40px rgba(0,0,0,.45);
    overflow: hidden;
  }
  .card--front { background: var(--card); }
  .card--back {
    background: var(--card-back);
    display: flex; align-items: center; justify-content: center;
  }

  .brand {
    position: absolute; top: 34px; left: 36px;
    display: flex; align-items: center; gap: 10px;
  }
  .brand__mark { width: 14px; height: 14px; background: var(--orange); }
  .brand__name {
    font-weight: 700; font-size: 20px; color: var(--white);
    letter-spacing: .5px;
  }
  .tagline {
    position: absolute; top: 78px; left: 36px;
    color: var(--orange); font-size: 12.5px; line-height: 1.4;
  }
  .contacts {
    position: absolute; left: 36px; bottom: 34px;
    list-style: none; color: var(--white); font-size: 12px; line-height: 1.55;
  }
  .contacts li { display: flex; align-items: center; gap: 8px; }
  .contacts svg { width: 11px; height: 11px; flex: none; }

  .person {
    position: absolute; right: 40px; bottom: 58px; text-align: left;
  }
  .person__name { font-size: 24px; font-weight: 700; line-height: 1.1; }
  .person__first { color: var(--orange); }
  .person__last { color: var(--white); }
  .person__role { color: var(--white); font-size: 14px; margin-top: 4px; }
  .accent-tab {
    position: absolute; right: 40px; bottom: 0;
    width: 44px; height: 28px; background: var(--orange);
  }

  .back__name {
    font-weight: 700; font-size: 30px; color: var(--emboss);
    letter-spacing: 1px;
    display: flex; align-items: center; gap: 14px;
  }
  .back__mark { width: 18px; height: 18px; background: var(--emboss); }
</style>
</head>
<body>
  <main class="stage">
    <section class="card card--front" aria-label="Business card front">
      <div class="brand">
        <span class="brand__mark"></span>
        <span class="brand__name">Coastline Premier Retreats</span>
      </div>
      <p class="tagline">Luxury Hotel &amp;<br>Resort Email Marketing</p>

      <ul class="contacts">
        <li>
          <svg viewBox="0 0 12 12" aria-hidden="true"><path d="M2.5 1h2l1 3-1.4 1a6 6 0 0 0 2.9 2.9L8 6.5l3 1v2A1.5 1.5 0 0 1 9.5 11 8.5 8.5 0 0 1 1 2.5 1.5 1.5 0 0 1 2.5 1z" fill="var(--orange)"/></svg>
          (555) 014-2758
        </li>
        <li>
          <svg viewBox="0 0 12 12" aria-hidden="true"><rect x="3" y="0.8" width="6" height="10.4" rx="1" fill="none" stroke="var(--orange)" stroke-width="1.2"/><circle cx="6" cy="9.3" r=".6" fill="var(--orange)"/></svg>
          (555) 019-7777
        </li>
        <li>
          <svg viewBox="0 0 12 12" aria-hidden="true"><circle cx="6" cy="6" r="5" fill="none" stroke="var(--orange)" stroke-width="1.1"/><ellipse cx="6" cy="6" rx="2.2" ry="5" fill="none" stroke="var(--orange)" stroke-width="1"/><path d="M1 6h10" stroke="var(--orange)" stroke-width="1"/></svg>
          www.coastlinepremierretreats.example
        </li>
        <li>
          <svg viewBox="0 0 12 12" aria-hidden="true"><rect x="0.8" y="2.3" width="10.4" height="7.4" rx="1" fill="none" stroke="var(--orange)" stroke-width="1.1"/><path d="M1 2.8l5 3.8 5-3.8" fill="none" stroke="var(--orange)" stroke-width="1.1"/></svg>
          info@coastlinepremierretreats.example
        </li>
      </ul>

      <div class="person">
        <p class="person__name"><span class="person__first">Marta</span> <span class="person__last">Kovalenko</span></p>
        <p class="person__role">Co-Founder</p>
      </div>
      <span class="accent-tab"></span>
    </section>

    <section class="card card--back" aria-label="Business card back">
      <div class="back__name">
        <span class="back__mark"></span>
        <span>Coastline Premier Retreats</span>
      </div>
    </section>
  </main>
</body>
</html>
```